Maple n Brook - Contact/Landing Page

I need a landing page which will essentially be the page that customers will go to from the 'website' link on QTV listing. It will provide a short overview of services which need to be selectable. a little further down can capture some contact details followed by a large Submit Now button etc...

I have some icon/logo's that can be utilised at the bottom of the page as industry type references.

Target Market(s)

End of Lease Cleaning Services

Industry/Entity Type

Cleaning Service

Colors

Designer to choose colors to be used in the design.

Requirements
Must have
• As per description
Should not have
• Colours to match my website maplenbrook.com.au

```html
<!DOCTYPE html>
<html lang="en">
<head>
<meta charset="utf-8">
<title>Maple n Brook – End of Lease Services</title>
<link href="https://fonts.googleapis.com/css2?family=Montserrat:wght@700&family=Roboto:wght@400;500&display=swap" rel="stylesheet">
<style>
  :root {
    --brand-blue: #3a76b9;
    --brand-light: #5bb4e8;
    --ink: #111418;
    --muted: #6a6a6a;
    --band-grey: #a0a0a0;
    --footer: #22252e;
    --white: #ffffff;
    --card-shadow: 0 1px 4px rgba(0,0,0,.18);
  }
  * { box-sizing: border-box; margin: 0; padding: 0; }
  html, body { width: 689px; height: 1200px; overflow: hidden; background: var(--white); }
  body { position: relative; font-family: "Roboto", Arial, sans-serif; color: var(--ink); }

  .hero { position: absolute; left: 0; top: 0; width: 689px; height: 337px; background: var(--brand-blue); }
  .brand { position: absolute; left: 0; right: 0; top: 120px; text-align: center; }
  .brand-mark { display: inline-block; width: 26px; height: 26px; border-radius: 50%; background: var(--white); vertical-align: middle; margin-right: 10px; }
  .brand-name { display: inline-block; vertical-align: middle; font-family: "Montserrat", Arial, sans-serif; font-weight: 700; font-size: 34px; color: var(--white); letter-spacing: 1px; }
  .hero-title { position: absolute; left: 0; right: 0; top: 285px; text-align: center; font-family: "Montserrat", Arial, sans-serif; font-weight: 700; font-size: 25px; color: var(--white); }

  .section-title { position: absolute; left: 0; right: 0; text-align: center; font-family: "Montserrat", Arial, sans-serif; font-weight: 700; font-size: 20px; }
  .services-title { top: 389px; color: var(--ink); }

  .service { position: absolute; top: 437px; width: 181px; height: 190px; }
  .service-photo { position: absolute; left: 0; top: 0; width: 181px; height: 127px; }
  .service-card { position: absolute; left: 5px; top: 115px; width: 170px; height: 71px; background: var(--white); box-shadow: var(--card-shadow); text-align: center; padding-top: 11px; }
  .service-name { display: flex; align-items: center; justify-content: center; gap: 9px; font-size: 13px; font-weight: 500; color: var(--ink); }
  .checkbox { width: 12px; height: 12px; border: 1.2px solid var(--brand-blue); display: inline-block; position: relative; }
  .checkbox svg { position: absolute; left: 0; top: 0; }
  .service-desc { margin-top: 7px; font-size: 8px; line-height: 13px; color: var(--muted); padding: 0 4px; }
  .photo-rooms { background: linear-gradient(180deg, #d9c4a6 0%, #efe6d6 45%, #9a5a28 100%); }
  .photo-carpet { background: linear-gradient(135deg, #d6d3cc 0%, #bfbbb3 55%, #cfccc5 100%); }
  .photo-insect { background: radial-gradient(ellipse at 55% 60%, #b56d2c 0%, #e0c497 40%, #eadbc2 100%); }

  .contact { position: absolute; left: 0; top: 680px; width: 689px; height: 262px; background: var(--band-grey); }
  .contact-title { top: 25px; color: var(--white); }
  .field { position: absolute; background: var(--white); font-size: 9px; color: var(--muted); padding: 0 10px; display: flex; align-items: center; }
  .field-tall { align-items: flex-start; padding-top: 9px; }
  .submit { position: absolute; left: 64px; top: 206px; width: 561px; height: 27px; background: var(--brand-blue); color: var(--white); font-size: 9px; font-weight: 500; display: flex; align-items: center; justify-content: center; }

  .partners { position: absolute; top: 1000px; left: 0; width: 689px; height: 60px; }
  .partner { position: absolute; top: 0; width: 134px; height: 60px; background: var(--white); box-shadow: var(--card-shadow); display: flex; align-items: center; justify-content: center; }
  .badge { border-radius: 4px; }
  .arrow { position: absolute; top: 19px; }

  .footer { position: absolute; left: 0; top: 1117px; width: 689px; height: 83px; background: var(--footer); color: var(--white); }
  .footer-email { position: absolute; left: 0; right: 0; top: 13px; display: flex; align-items: center; justify-content: center; gap: 14px; font-size: 12px; }
  .footer-rule { position: absolute; left: 64px; width: 561px; top: 51px; height: 1px; background: #c9cbd0; }
  .footer-copy { position: absolute; left: 64px; top: 59px; font-size: 7.5px; }
  .footer-licence { position: absolute; left: 545px; top: 60px; font-size: 7.5px; font-weight: 500; }
  .footer-licence span { color: var(--brand-blue); font-weight: 400; }
  .footer-code { position: absolute; left: 648px; top: 60px; font-size: 6.5px; }
</style>
</head>
<body>
  <header class="hero">
    <div class="brand"><span class="brand-mark"></span><span class="brand-name">MAPLE N BROOK</span></div>
    <h1 class="hero-title">END OF LEASE SERVICES</h1>
  </header>

  <h2 class="section-title services-title">OUR SERVICES</h2>

  <div class="service" style="left:64px">
    <div class="service-photo photo-rooms" role="img" aria-label="Bright empty living room with timber floors"></div>
    <div class="service-card">
      <div class="service-name"><span class="checkbox"><svg width="10" height="10" viewBox="0 0 10 10"><path d="M1.5 5.2 L4 7.6 L8.6 2.2" fill="none" stroke="#3a76b9" stroke-width="1.6"/></svg></span>CLEANING</div>
      <p class="service-desc">All interior cleaning carried out to property management requirments</p>
    </div>
  </div>

  <div class="service" style="left:254px">
    <div class="service-photo photo-carpet" role="img" aria-label="Vacuum head cleaning a light carpet"></div>
    <div class="service-card">
      <div class="service-name"><span class="checkbox"></span>CARPET CLEANING</div>
      <p class="service-desc">Carpet Steam Cleaning &nbsp;to Australian Standard Standard As 3733 : 1995</p>
    </div>
  </div>

  <div class="service" style="left:444px">
    <div class="service-photo photo-insect" role="img" aria-label="Close-up of a dead cockroach on a floor"></div>
    <div class="service-card">
      <div class="service-name"><span class="checkbox"></span>PEST CONTROL</div>
      <p class="service-desc">Mandatory requirements for pets on premises</p>
    </div>
  </div>

  <section class="contact">
    <h2 class="section-title contact-title">CONTACT US</h2>
    <div class="field" style="left:64px;top:68px;width:275px;height:27px">First Name</div>
    <div class="field" style="left:349px;top:68px;width:276px;height:27px">Last Name</div>
    <div class="field" style="left:64px;top:105px;width:275px;height:27px">Email</div>
    <div class="field" style="left:349px;top:105px;width:276px;height:27px">Phone Number</div>
    <div class="field field-tall" style="left:64px;top:142px;width:561px;height:54px">Subrub</div>
    <div class="submit">SUBMIT NOW</div>
  </section>

  <div class="partners">
    <svg class="arrow" style="left:24px" width="12" height="22" viewBox="0 0 12 22"><path d="M10 2 L2 11 L10 20" fill="none" stroke="#9a9a9a" stroke-width="1.6"/></svg>
    <div class="partner" style="left:64px"><div class="badge" style="width:90px;height:37px;background:#111"></div></div>
    <div class="partner" style="left:206px"><div class="badge" style="width:116px;height:32px;background:#c9303b"></div></div>
    <div class="partner" style="left:348px"><div class="badge" style="width:68px;height:42px;background:#2a4a9a"></div></div>
    <div class="partner" style="left:491px"><div class="badge" style="width:115px;height:35px;background:#8ab44a"></div></div>
    <svg class="arrow" style="left:653px" width="12" height="22" viewBox="0 0 12 22"><path d="M2 2 L10 11 L2 20" fill="none" stroke="#3a76b9" stroke-width="1.8"/></svg>
  </div>

  <footer class="footer">
    <div class="footer-email">
      <svg width="26" height="26" viewBox="0 0 26 26"><circle cx="13" cy="13" r="12" fill="none" stroke="#fff" stroke-width="1.4"/><circle cx="13" cy="13" r="9.5" fill="#fff"/><rect x="8.5" y="10" width="9" height="6.5" fill="none" stroke="#3a76b9" stroke-width="1"/><path d="M8.5 10 L13 13.6 L17.5 10" fill="none" stroke="#3a76b9" stroke-width="1"/></svg>
      <span>info@maplenbrook.com.au</span>
    </div>
    <div class="footer-rule"></div>
    <p class="footer-copy">Copyrights 2021 MAPLE N BROOK. All Rights Reserved</p>
    <p class="footer-licence">Pest Licence: <span>5170342</span></p>
    <p class="footer-code">C45</p>
  </footer>
</body>
</html>
```